Business card for law firm

Need business card for new law firm. Think confident, authoritative, conservative, but not stuffy or old-fashioned.

Contact Information for Business Card

Content for card - logo (uploaded), plus the following:

Paul Whitcombe (larger font)
Managing Partner (larger font, but not as large as name)
Level 9, 7 Ferris Lane
Sydney NSW 2000
Main Tel 02 9364 2710
Direct Tel 02 8472 3159
Email paul@qvlegal.com.au
www.qvlegal.com.au

Letterhead design should include logo plus:
Level 9, 7 Ferris Lane
Sydney NSW 2000
Tel 02 8472 3159
www.qvlegal.com.au

```html
<!DOCTYPE html>
<html lang="en">
<head>
<meta charset="utf-8">
<title>Quayvale Legal – Business Card</title>
<link rel="stylesheet" href="https://fonts.googleapis.com/css2?family=Cinzel:wght@500&family=Montserrat:wght@400&display=swap">
<style>
  :root {
    --backdrop: #1a1a1b;
    --card: #222223;
    --card-sheen: #2d2d2e;
    --ink-bright: #e6e6e6;
    --ink-soft: #c4c4c4;
    --ink-emboss: #3a3a3b;
    --rule: #6c6c6c;
  }
  * { margin: 0; padding: 0; box-sizing: border-box; }
  html, body { width: 1200px; height: 900px; overflow: hidden; background: var(--backdrop); }
  .sheet {
    width: 1200px; height: 900px;
    display: flex; flex-direction: column; align-items: center; justify-content: center; gap: 30px;
  }
  .card {
    width: 700px; height: 400px; position: relative;
    background: linear-gradient(125deg, var(--card) 0%, var(--card) 45%, var(--card-sheen) 75%, var(--card) 100%);
    box-shadow: 0 10px 30px rgba(0,0,0,.6);
  }
  .brand {
    display: flex; align-items: center; gap: 14px;
    font-family: "Montserrat", sans-serif; font-weight: 400; white-space: nowrap;
  }
  .brand-square { flex: none; }
  .brand-name { line-height: 1; }

  .card-front .brand { position: absolute; left: 0; right: 0; top: 176px; justify-content: center; color: var(--ink-soft); }
  .card-front .brand-square { width: 44px; height: 44px; background: var(--ink-soft); }
  .card-front .brand-name { font-size: 36px; }

  .card-back .brand { position: absolute; left: 30px; width: 310px; top: 180px; justify-content: center; color: var(--ink-emboss); }
  .card-back .brand-square { width: 34px; height: 34px; background: var(--ink-emboss); }
  .card-back .brand-name { font-size: 28px; }
  .divider { position: absolute; left: 360px; top: 80px; width: 1px; height: 230px; background: var(--rule); }

  .contact { position: absolute; left: 385px; top: 80px; color: var(--ink-bright); font-family: "Montserrat", sans-serif; }
  .contact-name { font-family: "Cinzel", serif; font-weight: 500; font-size: 24px; letter-spacing: .5px; }
  .contact-title { font-size: 15px; color: var(--ink-soft); margin-top: 2px; }
  .contact-address { font-size: 15px; line-height: 1.4; margin-top: 16px; }
  .contact-list { list-style: none; margin-top: 14px; font-size: 15px; }
  .contact-list li { display: flex; align-items: center; gap: 12px; line-height: 1.6; }
  .contact-list svg { width: 14px; height: 14px; fill: none; stroke: var(--ink-soft); stroke-width: 1.4; }
</style>
</head>
<body>
<main class="sheet">
  <section class="card card-front">
    <div class="brand">
      <div class="brand-square"></div>
      <div class="brand-name">Quayvale Legal</div>
    </div>
  </section>

  <section class="card card-back">
    <div class="brand">
      <div class="brand-square"></div>
      <div class="brand-name">Quayvale Legal</div>
    </div>
    <div class="divider"></div>
    <div class="contact">
      <div class="contact-name">PAUL WHITCOMBE</div>
      <div class="contact-title">Managing Partner</div>
      <div class="contact-address">Level 9, 7 Ferris Lane<br>Sydney NSW 2000</div>
      <ul class="contact-list">
        <li><svg viewBox="0 0 14 14"><path d="M3 1.5l2 2.5-1.2 1.5c.8 1.8 2 3 3.8 3.8L9 8l2.5 2-1 2C6 12 2 8 2 3.5z"/></svg>02 9364 2710</li>
        <li><svg viewBox="0 0 14 14"><rect x="3.5" y="1" width="7" height="12" rx="1"/><line x1="6" y1="11" x2="8" y2="11"/></svg>02 8472 3159</li>
        <li><svg viewBox="0 0 14 14"><rect x="1" y="3" width="12" height="8"/><path d="M1 3l6 4.5L13 3"/></svg>paul@qvlegal.com.au</li>
        <li><svg viewBox="0 0 14 14"><circle cx="7" cy="7" r="5.8"/><ellipse cx="7" cy="7" rx="2.5" ry="5.8"/><line x1="1.2" y1="7" x2="12.8" y2="7"/></svg>www.qvlegal.com.au</li>
      </ul>
    </div>
  </section>
</main>
</body>
</html>
```